Business card for Eyelash extension salon in Beverly Hills,California USA

We need new business card for our salon in Beverly Hills. The salon name is 'Lashvera' . We would like to have...Business name: Lashvera Name of person: will provide later Address 4720 N.Alder Crest Ave Beverly Hills , CA 90210 Phone: will provide later (Text only) Web: www.lashverastudio.example Snapgrid icon, Circlebook icon follow us for seasonal campaign and news @lashverastudiolounge Design should look elegant, high-end, clean, simple, cohesive with my brand. Please refer my brand board. Business name color will be metallic bronzy color. Im thinking grey background or white background. Thanks

Target Market(s)

25-35. Gender neutral. People who are in Entertainment business industry.
This is High-end Eyelash extension salon in Beverly Hills

Industry/Entity Type

Beauty Salon

Contact Information for Business Card

Business name: Lashvera
Name of person: will provide later
Address 4720 N.Alder Crest Ave Beverly Hills , CA 90210
Phone: will provide later (Text only)
Web: www.lashverastudio.example
Snapgrid icon, Circlebook icon
follow us for seasonal campaign and news @lashverastudiolounge

Requirements
Must have
• Beautiful, elegant, clean and simple look but very attractive and modern
Should not have
• We don't like too clutter, too busy designs.

```html
<!DOCTYPE html>
<html lang="en">
<head>
<meta charset="utf-8">
<title>Lashvera Business Card</title>
<link rel="stylesheet" href="https://fonts.googleapis.com/css2?family=Cormorant+Garamond:wght@500;600;700&family=Josefin+Sans:wght@400&display=swap">
<style>
  :root {
    --backdrop: #dedede;
    --card: #f6f6f6;
    --card-texture: #efefef;
    --bronze: #8a6a50;
    --ink: #4a4a4a;
    --muted: #b3b3b3;
  }
  * { margin: 0; padding: 0; box-sizing: border-box; }
  html, body { width: 1200px; height: 960px; overflow: hidden; }
  body { background: var(--backdrop); position: relative; font-family: "Cormorant Garamond", Georgia, serif; }

  .card {
    position: absolute;
    width: 600px; height: 343px;
    background: var(--card);
    overflow: hidden;
  }
  .card--back { left: 302px; top: 122px; }
  .card--front { left: 299px; top: 495px; }

  .card__texture {
    position: absolute; inset: 0;
    background: linear-gradient(180deg, var(--card) 0%, var(--card-texture) 100%);
  }

  /* Back: contact side */
  .holder { position: absolute; right: 358px; top: 146px; text-align: right; }
  .holder__name { font-size: 23px; font-weight: 700; color: var(--bronze); letter-spacing: 0.5px; line-height: 1.1; }
  .holder__role { font-size: 16px; font-weight: 700; color: var(--muted); letter-spacing: 0.4px; line-height: 1.1; }

  .divider { position: absolute; left: 271px; top: 121px; width: 1px; height: 100px; background: var(--ink); }

  .contacts { position: absolute; left: 298px; top: 120px; list-style: none; }
  .contacts__item { display: flex; align-items: flex-start; font-size: 15.5px; font-weight: 500; color: var(--ink); line-height: 18px; margin-bottom: 1px; }
  .contacts__item--address { margin-bottom: 7px; }
  .contacts__icon { width: 13px; height: 13px; margin: 3px 10px 0 0; flex: none; fill: var(--ink); }

  /* Front: brand side */
  .brand { position: absolute; left: 0; right: 40px; top: 92px; text-align: center; }
  .brand__name { font-size: 96px; font-weight: 500; color: var(--bronze); line-height: 1; letter-spacing: 1px; }
  .brand__place { position: absolute; left: 276px; top: 222px; font-family: "Josefin Sans", Arial, sans-serif; font-size: 11px; letter-spacing: 2.4px; color: var(--bronze); }

  .social { position: absolute; left: 170px; width: 246px; top: 293px; display: flex; align-items: center; gap: 10px; }
  .social__rule { flex: 1; height: 1px; background: var(--bronze); }
  .social__name { font-size: 14px; font-weight: 600; color: var(--bronze); letter-spacing: 0.3px; }
</style>
</head>
<body>

<section class="card card--back" aria-label="Card back with contact details">
  <div class="card__texture" role="img" aria-label="Soft light grey honeycomb texture"></div>
  <div class="holder">
    <p class="holder__name">MARA ELLISON</p>
    <p class="holder__role">CEO/FOUNDER</p>
  </div>
  <div class="divider"></div>
  <ul class="contacts">
    <li class="contacts__item contacts__item--address">
      <svg class="contacts__icon" viewBox="0 0 12 12"><path d="M6 0a4 4 0 0 0-4 4c0 3 4 8 4 8s4-5 4-8a4 4 0 0 0-4-4zm0 5.6A1.6 1.6 0 1 1 6 2.4a1.6 1.6 0 0 1 0 3.2z"/></svg>
      <span>4720 N.Alder Crest<br>Ave Beverly Hills, CA 90210</span>
    </li>
    <li class="contacts__item">
      <svg class="contacts__icon" viewBox="0 0 12 12"><path d="M2.4 0.6l2 2.2-1 1.4c.7 1.5 2 2.8 3.4 3.5l1.4-1 2.2 2-1 2.2C5.1 10.6 1.2 6.8 0.4 2z"/></svg>
      <span>310 555 0148</span>
    </li>
    <li class="contacts__item">
      <svg class="contacts__icon" viewBox="0 0 12 12"><path d="M0.5 2.5h11v7h-11z M0.5 2.5l5.5 4 5.5-4" fill="none" stroke="#4a4a4a" stroke-width="1.2"/></svg>
      <span>news@lashverastudiolounge</span>
    </li>
    <li class="contacts__item">
      <svg class="contacts__icon" viewBox="0 0 12 12"><circle cx="6" cy="6" r="5.4"/><path d="M3.5 3.5c1 .5 1.5 1.5 1 2.5s.5 2 1.5 2.5M7.5 2c-.5 1 0 2 1 2.3" fill="none" stroke="#f6f6f6" stroke-width="1"/></svg>
      <span>www.lashverastudio.example</span>
    </li>
  </ul>
</section>

<section class="card card--front" aria-label="Card front with brand name">
  <div class="card__texture" role="img" aria-label="Soft light grey honeycomb texture"></div>
  <div class="brand">
    <p class="brand__name">Lashvera</p>
  </div>
  <p class="brand__place">BEVERLY HILLS</p>
  <div class="social">
    <span class="social__rule"></span>
    <span class="social__name">Circlebook</span>
    <span class="social__name">Snapgrid</span>
    <span class="social__rule"></span>
  </div>
</section>

</body>
</html>
```